Biz Card

MARKETING today is the most rapidly changing business discipline. Media options to reach customers, actual customer preferences and consumer buying decisions change by the minute . . . no, by the second. The behavioral data generated by all aspects of the business and the new technologies that put the data to work together produce the potential to generate business intelligence and guide smart resource allocation to influence purchase and retention. However, to realize this potential, marketing professionals at all levels and in all organizations must continuously improve their skills not just from on-the-job training but by learning from masters in the field. The Bright Horizon Guild is the training center that serves this professional development need.model logos:msi.orgama.orgcontentmarketinginstitute.comBook covers on MarketingMetrics, Marketing Anaytics
Industry/Entity Type
Business
Contact Information for Business Card
Roy A. YoungCEOMarketing Science Academyphone: 310-601-4755email: roy@marketingscience.comAddress:437 South Rexford DriveBeverly Hills, CA 89377
Look and feel
Each slider illustrates characteristics of the customer's brand and the style your logo design should communicate.

```html
<!DOCTYPE html>
<html lang="en">
<head>
<meta charset="utf-8">
<title>Bright Horizon Guild – Business Card</title>
<link href="https://fonts.googleapis.com/css2?family=Roboto:wght@400;500;700;900&display=swap" rel="stylesheet">
<style>
  :root {
    --backdrop: #a8a6a6;
    --brand-red: #8b2a25;
    --ink-grey: #58585a;
    --text-grey: #4a4a4a;
    --paper: #f7f7f6;
    --stripe-dark: #5d5d5f;
  }
  * { margin: 0; padding: 0; box-sizing: border-box; }
  html, body {
    width: 1200px; height: 1200px; overflow: hidden;
    background: var(--backdrop);
    font-family: "Roboto", Arial, sans-serif;
  }
  .canvas { position: relative; width: 1200px; height: 1200px; }

  .card { position: absolute; width: 713px; height: 420px; }

  /* Front */
  .card-front { left: 238px; top: 117px; background: var(--brand-red); }
  .front-brand {
    position: absolute; left: 0; right: 0; top: 0; bottom: 0;
    display: flex; align-items: center; justify-content: center; gap: 18px;
  }
  .brand-name {
    font-weight: 900; text-transform: uppercase; letter-spacing: 0.5px;
    line-height: 1;
  }
  .front-brand .brand-name { color: #ffffff; font-size: 46px; }
  .brand-dot { width: 22px; height: 22px; border-radius: 50%; }
  .front-brand .brand-dot { background: #ffffff; }

  /* Back */
  .card-back { left: 230px; top: 643px; background: var(--paper); }
  .side-band { position: absolute; left: 0; top: 0; width: 60px; height: 100%; background: var(--brand-red); }
  .side-line { position: absolute; left: 60px; top: 0; width: 8px; height: 100%; background: var(--stripe-dark); }

  .back-brand {
    position: absolute; right: 26px; top: 54px;
    display: flex; align-items: center; gap: 14px;
  }
  .back-brand .brand-name { color: var(--brand-red); font-size: 36px; }
  .back-brand .brand-dot { background: var(--ink-grey); width: 18px; height: 18px; }

  .holder { position: absolute; left: 98px; top: 198px; }
  .holder-name { color: var(--brand-red); font-weight: 700; font-size: 25px; }
  .holder-role { color: var(--text-grey); font-size: 16px; margin-top: 8px; }

  .contact-list { position: absolute; left: 98px; top: 288px; list-style: none; }
  .contact-list li {
    display: flex; align-items: center; height: 23.7px;
    font-size: 17px; color: var(--text-grey);
  }
  .contact-list svg { width: 18px; height: 16px; margin-right: 17px; fill: var(--brand-red); }
</style>
</head>
<body>
<main class="canvas">

  <section class="card card-front" aria-label="Card front">
    <div class="front-brand">
      <span class="brand-name">Bright Horizon Guild</span>
      <span class="brand-dot"></span>
    </div>
  </section>

  <section class="card card-back" aria-label="Card back">
    <div class="side-band"></div>
    <div class="side-line"></div>

    <div class="back-brand">
      <span class="brand-name">Bright Horizon Guild</span>
      <span class="brand-dot"></span>
    </div>

    <div class="holder">
      <p class="holder-name">Neil P. Barton</p>
      <p class="holder-role">CEO</p>
    </div>

    <ul class="contact-list">
      <li>
        <svg viewBox="0 0 18 16" aria-hidden="true"><path d="M1 5c0-2 3-3 8-3s8 1 8 3v1h-4V4.5H5V6H1z"/><rect x="3" y="7" width="12" height="8" rx="1"/></svg>
        310-555-0182
      </li>
      <li>
        <svg viewBox="0 0 18 16" aria-hidden="true"><path d="M1 3h16v10H1z M2.5 4.5 9 9l6.5-4.5" fill="none" stroke="#8b2a25" stroke-width="2"/></svg>
        neil@brighthorizonguild.com
      </li>
      <li>
        <svg viewBox="0 0 18 16" aria-hidden="true"><g fill="none" stroke="#8b2a25" stroke-width="1.5"><circle cx="9" cy="8" r="6.5"/><ellipse cx="9" cy="8" rx="3" ry="6.5"/><path d="M2.5 8h13M3.5 4.5h11M3.5 11.5h11"/></g></svg>
        www.brighthorizonguild.com
      </li>
      <li>
        <svg viewBox="0 0 18 16" aria-hidden="true"><path d="M9 1a5 5 0 0 0-5 5c0 4 5 9.5 5 9.5s5-5.5 5-9.5a5 5 0 0 0-5-5zm0 7a2 2 0 1 1 0-4 2 2 0 0 1 0 4z"/></svg>
        912 North Calloway Lane Beverly Hills, CA 89377
      </li>
    </ul>
  </section>

</main>
</body>
</html>
```